IT Company based on Biology Business Needs a Professional Web Design

We need a professional business website design for a new company called 'Plume KEV'. We develop the machine learning solutions especially focused on deep learning algorithms for biology industry. Our initial product is a vision detection on biological images to help doctors diagnose the symptoms. We would like to see designs that use the color green.

Industry/Entity Type

Business

Number of Pages Required

5+ page

```html
<!DOCTYPE html>
<html lang="en">
<head>
<meta charset="utf-8">
<title>Plume KEV — Deep Learning Algorithms for Biology Industry</title>
<link href="https://fonts.googleapis.com/css2?family=Open+Sans:wght@400;600;700;800&family=Raleway:wght@300;400;500;600&display=swap" rel="stylesheet">
<style>
  :root{
    --white:#ffffff;
    --nav:#1f2327;
    --hero-deep:#0c2a44;
    --hero-mid:#1b5f8e;
    --hero-light:#3fa9d8;
    --lime:#5cc41a;
    --lime-light:#86d92c;
    --green:#1f9a3c;
    --green-dark:#0e7a2e;
    --footer:#0f6a2b;
    --text:#666a6e;
    --text-soft:#8a8e92;
    --heading:#4a4d50;
    --green-text:#3aa313;
    --rule:#d9dcde;
  }
  *{box-sizing:border-box;margin:0;padding:0}
  html,body{width:720px;height:1200px;overflow:hidden;background:var(--white)}
  body{position:relative;font-family:"Open Sans",Arial,sans-serif;color:var(--text)}
  .abs{position:absolute}

  /* header */
  .brand{left:102px;top:16px;display:flex;align-items:center;gap:6px}
  .brand-dot{width:14px;height:14px;border-radius:50%;background:var(--green)}
  .brand-name{font-family:"Raleway",Arial,sans-serif;font-weight:600;font-size:18px;color:var(--green);letter-spacing:-.3px}

  .main-nav{left:0;top:60px;width:720px;height:29px;background:var(--nav)}
  .main-nav a{position:absolute;top:8px;font-size:9.5px;color:var(--white);text-decoration:none;letter-spacing:.1px}

  /* hero */
  .hero{left:0;top:89px;width:720px;height:296px;
    background:radial-gradient(ellipse at 70% 40%,var(--hero-light) 0%,var(--hero-mid) 35%,var(--hero-deep) 80%)}
  .hero-kicker{left:104px;top:206px;font-weight:800;font-size:17.5px;color:var(--white);letter-spacing:.2px}
  .hero-title{left:104px;top:229px;font-weight:800;font-size:27px;color:var(--white);letter-spacing:.3px}
  .slider-dot{top:362px;width:10px;height:10px;border-radius:50%;background:var(--white)}
  .slider-dot.is-active{background:#e0a40c;border:1.5px solid var(--white)}

  /* feature band */
  .feature{top:385px;height:119px;color:var(--white)}
  .feature.alt{background:linear-gradient(135deg,#27a84a,var(--green-dark))}
  .feature.main{background:linear-gradient(135deg,var(--lime),var(--lime-light))}
  .feature h3{position:absolute;top:24px;font-family:"Open Sans",Arial,sans-serif;font-weight:600;font-size:11px;letter-spacing:.3px}
  .feature .bar{position:absolute;top:40px;width:16px;height:1.5px;background:var(--white)}
  .feature p{position:absolute;top:45px;width:148px;font-size:6.4px;line-height:11.6px;opacity:.9}
  .band-rule{left:0;top:504px;width:720px;height:1px;background:var(--rule)}

  /* about */
  .section-title{font-family:"Raleway",Arial,sans-serif;font-weight:400;color:var(--heading)}
  .about-title{left:101px;top:536px;font-size:20px}
  .about-lead{left:101px;top:572px;width:250px;font-size:7.6px;line-height:10px;color:var(--text)}
  .about-body{left:101px;top:600px;width:250px;font-size:5.9px;line-height:10.2px;color:var(--text-soft)}
  .btn{left:101px;top:648px;width:66px;height:19px;background:var(--green-dark);border-radius:2px;color:var(--white);
    font-size:6.8px;display:flex;align-items:center;justify-content:center;gap:4px;text-decoration:none}
  .how-title{left:376px;top:539px;font-size:15px}
  .how-photo{left:377px;top:569px;width:112px;height:85px;border:1px solid #e1e3e5;
    background:linear-gradient(135deg,#f3f4f5,#dcdfe2 55%,#b99a86)}
  .how-lead{left:496px;top:567px;width:125px;font-size:6.5px;line-height:10.5px;color:var(--text)}
  .how-body{left:496px;top:594px;width:125px;font-size:5.8px;line-height:11.2px;color:var(--text-soft)}
  .section-rule{left:0;top:705px;width:720px;height:1px;background:var(--rule)}

  /* research */
  .research-title{left:105px;top:728px;font-family:"Raleway",Arial,sans-serif;font-weight:400;font-size:16px;color:var(--green-dark)}
  .research-card{top:759px;width:161px}
  .research-photo{width:161px;height:98px}
  .research-card h4{margin-top:8px;margin-left:3px;font-size:8.8px;font-weight:600;color:var(--green-text);letter-spacing:.2px}
  .research-card p{margin-top:4px;margin-left:3px;width:155px;font-size:6.1px;line-height:11px;color:var(--text)}

  /* news */
  .news{left:0;top:954px;width:720px;height:184px;
    background:radial-gradient(ellipse at 70% 30%,#8ee13c 0%,var(--lime) 45%,#3ea812 100%)}
  .news-title{left:102px;top:981px;font-family:"Raleway",Arial,sans-serif;font-weight:400;font-size:17px;color:var(--white);display:flex;align-items:center;gap:8px}
  .news-item{top:1017px;width:160px;color:var(--white)}
  .news-date{display:inline-block;background:var(--white);color:#333;font-size:6.8px;padding:2px 12px 2px 6px;
    clip-path:polygon(0 0,100% 0,88% 100%,0 100%)}
  .news-item h4{margin-top:3px;font-size:9px;font-weight:400}
  .news-item p{margin-top:3px;font-size:6.3px;line-height:10.8px;opacity:.92}
  .news-item a{display:block;margin-top:5px;font-size:7.8px;color:var(--white);text-decoration:none}

  /* footer */
  .site-footer{left:0;top:1138px;width:720px;height:62px;background:var(--footer);color:var(--white)}
  .footer-nav{position:absolute;left:102px;top:20px;font-size:7.2px;font-weight:700;letter-spacing:.2px}
  .footer-nav span{margin:0 3px;font-weight:400}
  .copyright{position:absolute;left:102px;top:37px;font-size:5.8px;opacity:.85}
  .social{position:absolute;top:18px;width:17px;height:17px;border-radius:50%;border:1px solid var(--white)}
</style>
</head>
<body>

<header>
  <div class="abs brand"><span class="brand-dot"></span><span class="brand-name">Plume KEV</span></div>
  <nav class="abs main-nav">
    <a style="left:127px">HOME</a>
    <a style="left:188px">ABOUT US</a>
    <a style="left:267px">TECHNOLOGY</a>
    <a style="left:362px">PRODUCTS</a>
    <a style="left:444px">OUR DOCTORS</a>
    <a style="left:542px">RESOURCES</a>
  </nav>
</header>

<section class="abs hero" role="img" aria-label="Glowing blue DNA double helix strands"></section>
<div class="abs hero-kicker">DEEP LEARNING ALGORITHMS</div>
<div class="abs hero-title">FOR BIOLOGY INDUSTRY</div>
<span class="abs slider-dot is-active" style="left:337px"></span>
<span class="abs slider-dot" style="left:349px"></span>
<span class="abs slider-dot" style="left:361px"></span>
<span class="abs slider-dot" style="left:373px"></span>

<section>
  <div class="abs feature main" style="left:0;width:262px">
    <h3 style="left:104px">WHAT WE DO</h3><span class="bar" style="left:104px"></span>
    <p style="left:104px">Morbi diam mauris viverra in gravida eu mattis in ante Morbi eget arcu Morbi porta libero id ullamcorper nonummy nibh ligula pulvinar metus eget consecte</p>
  </div>
  <div class="abs feature alt" style="left:262px;width:195px">
    <h3 style="left:24px">TECHNOLOGY</h3><span class="bar" style="left:24px"></span>
    <p style="left:24px">Morbi diam mauris viverra in gravida eu mattis in ante Morbi eget arcu Morbi porta libero id ullamcorper nonummy nibh ligula pulvinar metus eget consecte</p>
  </div>
  <div class="abs feature main" style="left:457px;width:263px">
    <h3 style="left:21px">OUR DOCTORS</h3><span class="bar" style="left:21px"></span>
    <p style="left:21px">Morbi diam mauris viverra in gravida eu mattis in ante Morbi eget arcu Morbi porta libero id ullamcorper nonummy nibh ligula pulvinar metus eget consecte</p>
  </div>
</section>
<div class="abs band-rule"></div>

<section>
  <h2 class="abs section-title about-title">About Plume Kev</h2>
  <p class="abs about-lead">Duis sed tellus et tortor vestibulum gravida Praesent elementum elit at tellus Curabitur metus ipsum luctus eu males</p>
  <p class="abs about-body">Maecenas aliquet velit vel turpis Mauris neque metus malesuada nec ultricies sit amet porttitor mattis enim In massa libero interdum nec interdum vel blandit sed nulla in ullamcorper est eget tempor cursus neque mi consectetuer mi a ultricies massa est sed nisl Class aptent taciti sociosqu ad litora torquent pe</p>
  <a class="abs btn">READ MORE
    <svg width="5" height="7" viewBox="0 0 5 7"><path d="M1 1l2.5 2.5L1 6" fill="none" stroke="#fff" stroke-width="1"/></svg></a>

  <h2 class="abs section-title how-title">How it Works</h2>
  <div class="abs how-photo" role="img" aria-label="Scientist looking into a microscope in a bright laboratory"></div>
  <p class="abs how-lead">aecenas aliquet velit vel turpis Mauris neque metus malesuada</p>
  <p class="abs how-body">nec ultricies sit amet porttitor mattis enim In massa libero interdum nec interdum vel blandit sed nulla In ullamcorper est eget tempor cursus neque mi consectetuer mi a ultricies massa est sed nisl</p>
</section>
<div class="abs section-rule"></div>

<section>
  <h2 class="abs research-title">Latest Research</h2>
  <article class="abs research-card" style="left:102px">
    <div class="research-photo" role="img" aria-label="Gloved hands adjusting a laboratory microscope" style="background:linear-gradient(135deg,#e8eef4,#9fb6cc 60%,#3b5f86)"></div>
    <h4>Morbi diam mauris viverra</h4>
    <p>gravida eu mattis in ante Morbi eget arcu Morbi porta libero id ullamcorper nonummy nibh ligula pulvinar metus eget consectetuer</p>
  </article>
  <article class="abs research-card" style="left:280px">
    <div class="research-photo" role="img" aria-label="Microscope view of a stained plant stem section" style="background:linear-gradient(160deg,#eef1f3,#b9c6d4 55%,#a27a92)"></div>
    <h4>Morbi diam mauris viverra</h4>
    <p>gravida eu mattis in ante Morbi eget arcu Morbi porta libero id ullamcorper nonummy nibh ligula pulvinar metus eget consectetuer</p>
  </article>
  <article class="abs research-card" style="left:458px">
    <div class="research-photo" role="img" aria-label="Researchers in protective suits working with lab flasks" style="background:linear-gradient(135deg,#0e3f8f,#2f7fd0 50%,#b5d6ef 80%,#d89a3a)"></div>
    <h4>Morbi diam mauris viverra</h4>
    <p>gravida eu mattis in ante Morbi eget arcu Morbi porta libero id ullamcorper nonummy nibh ligula pulvinar metus eget consectetuer</p>
  </article>
</section>

<section class="abs news" aria-label="Latest News"></section>
<h2 class="abs news-title">Latest News
  <svg width="26" height="22" viewBox="0 0 26 22"><g fill="#fff"><circle cx="6" cy="4" r="2.5"/><circle cx="16" cy="3" r="2"/><circle cx="3" cy="12" r="2"/><circle cx="22" cy="11" r="2.5"/><circle cx="8" cy="19" r="2"/><circle cx="18" cy="19" r="2.5"/></g></svg>
</h2>
<article class="abs news-item" style="left:102px">
  <span class="news-date">15 JAN 2016</span>
  <h4>Mabitur vel mi sit</h4>
  <p>Morbi diam mauris viverra in gravida eu mattis in ante Morbi eget arcu Morbi porta libero id ullamcorper nonummy nibh ligula</p>
  <a>Read More</a>
</article>
<article class="abs news-item" style="left:282px">
  <span class="news-date">19 JAN 2016</span>
  <h4>Proin dui lectus cursus eu mattis</h4>
  <p>Morbi diam mauris viverra in gravida eu mattis in ante Morbi eget arcu Morbi porta libero id ullamcorper nonummy nibh ligula</p>
  <a>Read More</a>
</article>
<article class="abs news-item" style="left:462px">
  <span class="news-date">18 JAN 2016</span>
  <h4>Aliquam erat volutpat Quisque</h4>
  <p>Morbi diam mauris viverra in gravida eu mattis in ante Morbi eget arcu Morbi porta libero id ullamcorper nonummy nibh ligula</p>
  <a>Read More</a>
</article>

<footer class="abs site-footer">
  <div class="footer-nav">HOME<span>|</span>ABOUT US<span>|</span>TECHNOLOGY<span>|</span>PRODUCTS<span>|</span>NEWS<span>|</span>CONTACT</div>
  <div class="copyright">© 2015 Company Name &nbsp;All right reserved &nbsp;Term of Use</div>
  <span class="social" style="left:552px"></span>
  <span class="social" style="left:570px"></span>
  <span class="social" style="left:588px"></span>
  <span class="social" style="left:606px"></span>
</footer>

</body>
</html>
```